Australian Trucking Company Requires Professional Looking Stationary

We require a professional looking stationary design that incorporates our newly designed logo.

Our business, called "Brell Haulage Contracting", provides contracting work, transport and logistics to business in Western Australia particularly with links to the mining sector.

We are a small business looking to expand and our new logo and our new stationary will help develop our brand image in our market place.

Target Market(s)

Businesses and Corporation with links to the Mining Sector

Industry/Entity Type

Small Business

Requirements
Must have
• The letterhead must have the following details:
The new logo

Text saying: "Brell Holdings Pty Ltd (ACN 582 316 907) ATF The Brell Discretionary Trust T/AS"
"ABN 71 834 209 553"
Address "P.O Box 817 Wattlegrove WA, 6958"
Phone: 08 9352 7140
Email: brellhaul@mailbox-example.com.au

The text on the letterhead should be editable as the details are likely to change in the near future. Provision should be made for a website address all though one isn't available at the moment.

The styling, layout and font text is entirely up to the designer.

```html
<!DOCTYPE html>
<html lang="en">
<head>
<meta charset="utf-8">
<title>Brell Haulage Contracting – Business Card</title>
<link rel="stylesheet" href="https://fonts.googleapis.com/css2?family=Open+Sans:wght@400;600;700&display=swap">
<style>
  :root {
    --backdrop: #e9e6e2;
    --card: #ffffff;
    --brand-red: #c8161e;
    --brand-red-dark: #7e0a10;
    --ink: #222222;
    --ink-soft: #555555;
    --on-red: #ffffff;
  }
  * { box-sizing: border-box; margin: 0; padding: 0; }
  html, body {
    width: 1200px; height: 426px; overflow: hidden;
    background: var(--backdrop);
    font-family: "Open Sans", Arial, sans-serif;
  }
  .canvas { position: relative; width: 1200px; height: 426px; }
  .card {
    position: absolute; width: 519px; height: 296px;
    background: var(--card); border-radius: 22px;
    box-shadow: 0 3px 10px rgba(0,0,0,.18);
  }
  .card--front { left: 77px; top: 62px; }
  .card--back  { left: 617px; top: 57px; }

  .brand-name {
    position: absolute; color: var(--brand-red);
    font-weight: 700; text-transform: uppercase; line-height: 1.02;
  }
  .card--front .brand-name { left: 175px; top: 38px; font-size: 33px; }
  .brand-mark {
    position: absolute; left: 40px; top: 46px; width: 110px; height: 110px;
    background: var(--brand-red); border-radius: 4px;
  }
  .card--back .brand-name {
    left: 0; right: 0; top: 92px; text-align: center; font-size: 38px;
  }

  .person { position: absolute; left: 60px; top: 178px; white-space: nowrap; }
  .person__name { color: var(--brand-red); font-weight: 700; font-size: 17px; }
  .person__role { color: var(--ink-soft); font-size: 13px; }

  .entity {
    position: absolute; left: 20px; width: 262px; top: 228px;
    text-align: center; color: var(--ink); font-size: 11px; line-height: 17px;
  }
  .entity__abn { margin-top: 3px; }

  .contact-panel {
    position: absolute; left: 308px; top: 178px; width: 200px; height: 98px;
    border-radius: 10px; color: var(--on-red);
    background: linear-gradient(180deg, var(--brand-red) 0%, var(--brand-red-dark) 100%);
    box-shadow: 0 6px 10px rgba(0,0,0,.35);
    padding: 10px 0 0 20px; font-size: 11px; line-height: 14px;
  }
  .contact-panel__address { margin-bottom: 10px; }
  .contact-line { display: flex; align-items: center; gap: 5px; height: 18px; white-space: nowrap; }
  .contact-line svg { width: 11px; height: 11px; flex: none; fill: var(--on-red); }
  .contact-line--email { font-size: 10px; }
</style>
</head>
<body>
<main class="canvas">
  <section class="card card--front" aria-label="Business card front">
    <span class="brand-mark" aria-hidden="true"></span>
    <h1 class="brand-name">Brell<br>Haulage<br>Contracting</h1>

    <p class="person"><span class="person__name">Persons name,</span> <span class="person__role">Manager</span></p>

    <div class="entity">
      <p>Brell Holdings Pty Ltd (ACN 582 316 907)</p>
      <p>ATF The Brell Discretionary Trust T/AS</p>
      <p class="entity__abn">ABN 71 834 209 553</p>
    </div>

    <address class="contact-panel">
      <p class="contact-panel__address">P.O Box 817<br>Wattlegrove WA, 6958</p>
      <p class="contact-line">
        <svg viewBox="0 0 24 24" aria-hidden="true"><path d="M6.6 10.8a15 15 0 0 0 6.6 6.6l2.2-2.2a1 1 0 0 1 1-.25 11.4 11.4 0 0 0 3.6.57 1 1 0 0 1 1 1V20a1 1 0 0 1-1 1A17 17 0 0 1 3 4a1 1 0 0 1 1-1h3.5a1 1 0 0 1 1 1 11.4 11.4 0 0 0 .57 3.6 1 1 0 0 1-.25 1z"/></svg>
        08 9352 7140
      </p>
      <p class="contact-line contact-line--email">
        <svg viewBox="0 0 24 24" aria-hidden="true"><path d="M2 5h20v14H2zm2 2v.5l8 5 8-5V7zm0 2.8V17h16V9.8l-8 5z"/></svg>
        brellhaul@mailbox-example.com.au
      </p>
    </address>
  </section>

  <section class="card card--back" aria-label="Business card back">
    <p class="brand-name">Brell<br>Haulage<br>Contracting</p>
  </section>
</main>
</body>
</html>
```